New & Improved KIVORA Business Card

I would like a two sided business card one side dedicated to home automation (security camera installation, television & sound bar mounting (hidden wires optional) , sink installation, fireplace mounting, chandelier installation and one side dedicated to all electronic repairs, In ex: plume band repairs, computer, zTab, laptop repairs, Velofon's, Korvex and etc.. Using the colors on this flyer. The phone number &email I want on both sides is (555) 214-3907 & Tech@Kivora.help. SAME COLOR AS THE FLYER ATTACHED.

Target Market(s)

EVERYONE.

Contact Information for Business Card

I would like a two sided business card one side dedicated to home automation (security camera installation, television & sound bar mounting (hidden wires optional) , sink installation, fireplace mounting, chandelier installation and one side dedicated to all electronic repairs, In ex: plume band repairs, computer, zTab, laptop repairs, Velofon's, Korvex and etc.. Using the colors on this flyer. The phone number &email I want on both sides is (555) 214-3907 & Tech@Kivora.help

Requirements
Must have
• -TV MOUNTING
-HOME AUTOMATION
-SECURITY CAMERA INSTALLATION
-ALL ELECTRONIC REPAIRS
- (555) 214-3907
-Tech@Kivora.help
-SAME COLOR AS THE FLYER
Nice to have
• Same colors & concept as the flyer attached below.
Should not have
• DO NOT DO A DIFF COLOR I WANT SAME COLOR AS THE FLYER ATTACHED.

```html
<!DOCTYPE html>
<html lang="en">
<head>
<meta charset="utf-8">
<title>KIVORA Business Card</title>
<link href="https://fonts.googleapis.com/css2?family=Montserrat:wght@500;600;700&display=swap" rel="stylesheet">
<style>
  :root {
    --brand-pink: #ec268f;
    --paper-white: #f2f2f2;
    --ink-grey: #555555;
    --backdrop: #3e3e3e;
    --on-pink: #ffffff;
  }
  * { box-sizing: border-box; margin: 0; padding: 0; }
  html, body {
    width: 1200px;
    height: 1126px;
    overflow: hidden;
    background: var(--backdrop);
    font-family: "Montserrat", Arial, sans-serif;
  }
  .card-sheet {
    position: relative;
    width: 1200px;
    height: 1126px;
  }
  .card {
    position: absolute;
    left: 150px;
    width: 900px;
    height: 514px;
    display: flex;
    flex-direction: column;
    align-items: center;
    justify-content: center;
    box-shadow: 0 6px 18px rgba(0,0,0,0.35);
  }
  .card--services {
    top: 32px;
    background: var(--brand-pink);
    color: var(--on-pink);
  }
  .card--contact {
    top: 580px;
    background: var(--paper-white);
  }
  .wordmark {
    font-weight: 700;
    font-size: 96px;
    letter-spacing: 22px;
    line-height: 1;
    margin-right: -22px;
  }
  .card--services .wordmark { color: var(--on-pink); margin-bottom: 70px; }
  .card--contact .wordmark { color: var(--brand-pink); margin-bottom: 44px; }
  .service-list {
    list-style: none;
    text-align: left;
    font-weight: 600;
    font-size: 22px;
    letter-spacing: 2px;
    line-height: 1.75;
  }
  .service-list .divider { padding: 0 18px; }
  .contact-row {
    display: flex;
    align-items: center;
    gap: 56px;
    font-weight: 600;
    font-size: 28px;
    letter-spacing: 2px;
    color: var(--ink-grey);
  }
  .contact-item {
    display: flex;
    align-items: center;
    gap: 14px;
  }
  .contact-icon { fill: var(--brand-pink); flex: none; }
</style>
</head>
<body>
<main class="card-sheet">
  <section class="card card--services" aria-label="Card front: services">
    <h1 class="wordmark">KIVORA</h1>
    <ul class="service-list">
      <li>TV MOUNTING<span class="divider">|</span>SECURITY CAMERA INSTALLATION</li>
      <li>HOME AUTOMATION<span class="divider">|</span>ALL ELECTRONIC REPAIRS</li>
    </ul>
  </section>

  <section class="card card--contact" aria-label="Card back: contact">
    <h2 class="wordmark">KIVORA</h2>
    <div class="contact-row">
      <div class="contact-item">
        <svg class="contact-icon" width="26" height="30" viewBox="0 0 24 24" aria-hidden="true">
          <path d="M6.6 10.8a15.1 15.1 0 0 0 6.6 6.6l2.2-2.2a1 1 0 0 1 1-.25c1.1.37 2.3.57 3.6.57a1 1 0 0 1 1 1V20a1 1 0 0 1-1 1A17 17 0 0 1 3 4a1 1 0 0 1 1-1h3.5a1 1 0 0 1 1 1c0 1.25.2 2.45.57 3.57a1 1 0 0 1-.25 1z"/>
        </svg>
        <span class="contact-text">(555) 214-3907</span>
      </div>
      <div class="contact-item">
        <svg class="contact-icon" width="40" height="28" viewBox="0 0 40 28" aria-hidden="true">
          <path d="M0 0h40v28H0z M3 3l17 13L37 3z" fill-rule="evenodd"/>
        </svg>
        <span class="contact-text">Tech@Kivora.help</span>
      </div>
    </div>
  </section>
</main>
</body>
</html>
```